Multiple website banners for a shopify theme

I need custom designed banners for a destributor webpage.

We will be selling products in our local store from a supplier https://glimmorabath.co.uk (you can get the ideas from their site).

We need custom desings:
- 2-3x 1920x745
- 1x 960x960
- 2x 480x480
- 1x 960*480
All of theme need to nicely fit together as shown in the uploaded layout screenshot (website_banner_layout).
In Google drive link there are products pictures which must be used in the banners.

https://files.quorvane.net/share/folders/7TkpWq2LmXe9VbNa4cHsYdRuF3jGz8Qo?mode=view

Kids, Cosmetics market

Cosmetics

• Playful elements

```html
<!DOCTYPE html>
<html lang="en">
<head>
<meta charset="utf-8">
<title>Tiny Toasties – Square Banner</title>
<link rel="stylesheet" href="https://fonts.googleapis.com/css2?family=Abril+Fatface&display=swap">
<style>
  :root {
    --pink: #ec4c9b;
    --white: #ffffff;
    --melt-teal: #3f9f86;
    --melt-teal-light: #5cb89d;
  }
  html, body {
    margin: 0;
    padding: 0;
    width: 1200px;
    height: 1200px;
    overflow: hidden;
  }
  .banner {
    position: relative;
    width: 1200px;
    height: 1200px;
    background: var(--pink);
    overflow: hidden;
  }
  .banner__title {
    position: absolute;
    left: 82px;
    top: 74px;
    margin: 0;
    font-family: "Abril Fatface", Georgia, serif;
    font-weight: 400;
    font-size: 146px;
    line-height: 176px;
    color: var(--white);
    letter-spacing: 1px;
  }
  .banner__product {
    position: absolute;
    left: 0;
    top: 500px;
    width: 680px;
    height: 700px;
  }
  .brand {
    position: absolute;
    right: 40px;
    bottom: 40px;
    display: flex;
    align-items: center;
    gap: 20px;
  }
  .brand__dot {
    width: 104px;
    height: 104px;
    border-radius: 50%;
    background: var(--white);
  }
  .brand__name {
    font-family: "Abril Fatface", Georgia, serif;
    font-weight: 400;
    color: var(--white);
    font-size: 46px;
    line-height: 50px;
    letter-spacing: 2px;
  }
</style>
</head>
<body>
  <main class="banner">
    <h1 class="banner__title">Tiny<br>Toasties</h1>

    <svg class="banner__product" viewBox="0 0 680 700" role="img"
         aria-label="Product photo: a cluster of round teal wax melts embossed with the brand initial">
      <defs>
        <radialGradient id="meltTone" cx="40%" cy="45%" r="70%">
          <stop offset="0%" stop-color="var(--melt-teal-light)"/>
          <stop offset="100%" stop-color="var(--melt-teal)"/>
        </radialGradient>
      </defs>
      <path d="M0 20 C60 0 130 10 180 40 C230 0 330 -10 380 40 C430 60 470 90 490 150
               C560 170 610 230 600 320 C650 360 680 430 670 520 C665 600 630 660 600 700
               L0 700 Z" fill="url(#meltTone)"/>
    </svg>

    <div class="brand">
      <span class="brand__dot"></span>
      <span class="brand__name">GLIMMORA<br>KOZMETIKA</span>
    </div>
  </main>
</body>
</html>
```